New Business Card Design Project

Use the flyer uploaded and website www.brightoakbuilders.com for inspiration.
List Our Services on Backside of business cards
Marcus Delling
Harborline Builders Inc.
Licensed General Contractors
858-471-6093

Contact Information for Business Card

Use the flyer uploaded and website www.brightoakbuilders.com for inspiration. List Our Services on Backside of business cards Marcus Delling Harborline Builders Inc. Licensed General Contractors 858-471-6093

```html
<!DOCTYPE html>
<html lang="en">
<head>
<meta charset="utf-8">
<title>Harborline Builders – Business Cards</title>
<link href="https://fonts.googleapis.com/css2?family=Open+Sans:wght@400;600&family=Roboto:wght@400;500;900&display=swap" rel="stylesheet">
<style>
  :root {
    --backdrop: #262626;
    --card: #222226;
    --edge: #e51d25;
    --red: #ea1c24;
    --blue: #5b80d2;
    --white: #ffffff;
  }
  * { box-sizing: border-box; margin: 0; padding: 0; }
  html, body { width: 1200px; height: 780px; overflow: hidden; background: var(--backdrop); }
  .stage {
    position: relative; width: 1200px; height: 780px;
    display: flex; align-items: center; justify-content: center; gap: 40px;
  }
  .card {
    position: relative; width: 540px; height: 310px;
    background: var(--card); border-radius: 22px;
    border: 2px solid var(--edge);
    box-shadow: 0 18px 40px rgba(0,0,0,.55);
    overflow: hidden; color: var(--white);
  }

  /* brand name block */
  .brand { display: flex; align-items: center; gap: 10px; justify-content: center; }
  .brand-mark { width: 14px; height: 14px; background: var(--white); flex: none; }
  .brand-name {
    font-family: 'Roboto', sans-serif; font-weight: 400; font-size: 24px;
    letter-spacing: 4px; text-transform: uppercase; color: var(--white); white-space: nowrap;
  }

  /* services side */
  .card--services .brand { margin-top: 64px; }
  .guarantee {
    margin-top: 34px; text-align: center;
    font-family: 'Roboto', sans-serif; font-weight: 900; font-size: 13px; color: var(--red);
    letter-spacing: .3px;
  }
  .specializing {
    margin-top: 2px; text-align: center;
    font-family: 'Roboto', sans-serif; font-weight: 900; font-size: 12px; color: var(--blue);
  }
  .service-list { margin-top: 12px; list-style: none; padding: 0 26px; }
  .service-row {
    display: flex; justify-content: center; gap: 8px; flex-wrap: nowrap;
    font-family: 'Roboto', sans-serif; font-size: 10.5px; line-height: 19px; color: var(--white);
  }
  .service { display: inline-flex; align-items: center; gap: 3px; white-space: nowrap; }
  .tick { width: 9px; height: 9px; flex: none; }

  /* contact side */
  .title-block { position: absolute; right: 0; top: 40px; display: flex; align-items: stretch; }
  .title-text { text-align: right; padding-right: 10px; padding-top: 2px; }
  .person-name {
    font-family: 'Roboto', sans-serif; font-weight: 900; font-size: 24px;
    color: var(--red); text-transform: uppercase; letter-spacing: .5px; line-height: 1;
  }
  .person-role {
    margin-top: 5px; font-family: 'Open Sans', sans-serif; font-size: 11px; color: var(--white);
  }
  .title-bar { width: 22px; background: var(--red); }

  .card--contact .brand { position: absolute; left: 40px; top: 112px; justify-content: flex-start; }

  .contact { position: absolute; left: 56px; bottom: 30px; font-family: 'Open Sans', sans-serif; }
  .company { font-size: 13px; margin-bottom: 10px; color: var(--white); }
  .contact-list { list-style: none; }
  .contact-item { display: flex; align-items: center; gap: 10px; font-size: 12.5px; line-height: 22px; color: var(--white); }
  .contact-icon { width: 13px; height: 13px; flex: none; }
</style>
</head>
<body>
<main class="stage">

  <section class="card card--services" aria-label="Card back: services">
    <div class="brand">
      <span class="brand-mark"></span>
      <span class="brand-name">Harborline Builders</span>
    </div>
    <p class="guarantee">OUR SERVICES ARE 100% GUARANTEED</p>
    <p class="specializing">SPECIALIZING IN:</p>
    <ul class="service-list">
      <li class="service-row">
        <span class="service"><svg class="tick" viewBox="0 0 10 10"><circle cx="5" cy="5" r="4.2" fill="none" stroke="#ea1c24" stroke-width="1"/><path d="M2.8 5.1l1.6 1.6 3-3.4" fill="none" stroke="#ea1c24" stroke-width="1.2"/></svg>Remodel: Kitchen &amp; Bath</span>
        <span class="service"><svg class="tick" viewBox="0 0 10 10"><circle cx="5" cy="5" r="4.2" fill="none" stroke="#ea1c24" stroke-width="1"/><path d="M2.8 5.1l1.6 1.6 3-3.4" fill="none" stroke="#ea1c24" stroke-width="1.2"/></svg>Painting: Interior &amp; Exterior</span>
        <span class="service"><svg class="tick" viewBox="0 0 10 10"><circle cx="5" cy="5" r="4.2" fill="none" stroke="#ea1c24" stroke-width="1"/><path d="M2.8 5.1l1.6 1.6 3-3.4" fill="none" stroke="#ea1c24" stroke-width="1.2"/></svg>Flooring: Carpet, Vinyl, Wood</span>
      </li>
      <li class="service-row">
        <span class="service"><svg class="tick" viewBox="0 0 10 10"><circle cx="5" cy="5" r="4.2" fill="none" stroke="#ea1c24" stroke-width="1"/><path d="M2.8 5.1l1.6 1.6 3-3.4" fill="none" stroke="#ea1c24" stroke-width="1.2"/></svg>Window &amp; Door Replacement</span>
        <span class="service"><svg class="tick" viewBox="0 0 10 10"><circle cx="5" cy="5" r="4.2" fill="none" stroke="#ea1c24" stroke-width="1"/><path d="M2.8 5.1l1.6 1.6 3-3.4" fill="none" stroke="#ea1c24" stroke-width="1.2"/></svg>Plumbing: Repairs &amp; Upgrades</span>
        <span class="service"><svg class="tick" viewBox="0 0 10 10"><circle cx="5" cy="5" r="4.2" fill="none" stroke="#ea1c24" stroke-width="1"/><path d="M2.8 5.1l1.6 1.6 3-3.4" fill="none" stroke="#ea1c24" stroke-width="1.2"/></svg>Energy-Efficient Upgrades</span>
      </li>
      <li class="service-row">
        <span class="service"><svg class="tick" viewBox="0 0 10 10"><circle cx="5" cy="5" r="4.2" fill="none" stroke="#ea1c24" stroke-width="1"/><path d="M2.8 5.1l1.6 1.6 3-3.4" fill="none" stroke="#ea1c24" stroke-width="1.2"/></svg>Deck &amp; Patio Construction</span>
        <span class="service"><svg class="tick" viewBox="0 0 10 10"><circle cx="5" cy="5" r="4.2" fill="none" stroke="#ea1c24" stroke-width="1"/><path d="M2.8 5.1l1.6 1.6 3-3.4" fill="none" stroke="#ea1c24" stroke-width="1.2"/></svg>Water &amp; Mold Damage</span>
        <span class="service"><svg class="tick" viewBox="0 0 10 10"><circle cx="5" cy="5" r="4.2" fill="none" stroke="#ea1c24" stroke-width="1"/><path d="M2.8 5.1l1.6 1.6 3-3.4" fill="none" stroke="#ea1c24" stroke-width="1.2"/></svg>Garage Renovation</span>
      </li>
    </ul>
  </section>

  <section class="card card--contact" aria-label="Card front: contact">
    <div class="title-block">
      <div class="title-text">
        <p class="person-name">Marcus Delling</p>
        <p class="person-role">Licensed General Contractors</p>
      </div>
      <span class="title-bar"></span>
    </div>

    <div class="brand">
      <span class="brand-mark"></span>
      <span class="brand-name">Harborline Builders</span>
    </div>

    <div class="contact">
      <p class="company">Harborline Builders Inc.</p>
      <ul class="contact-list">
        <li class="contact-item">
          <svg class="contact-icon" viewBox="0 0 16 16"><path d="M3.5 1.5l2.5 2.8-1.4 1.8c.9 2 2.4 3.5 4.4 4.4l1.8-1.4 2.8 2.5-1.6 2.2C6.8 13.5 2.5 9.2 1.3 3.1z" fill="#ea1c24"/></svg>
          858-471-6093
        </li>
        <li class="contact-item">
          <svg class="contact-icon" viewBox="0 0 16 16"><rect x="1" y="3" width="14" height="10" rx="1" fill="#ea1c24"/><path d="M1.5 3.6L8 9l6.5-5.4" fill="none" stroke="#222226" stroke-width="1.3"/></svg>
          info@brightoakbuilders.com
        </li>
        <li class="contact-item">
          <svg class="contact-icon" viewBox="0 0 16 16"><circle cx="8" cy="8" r="6.6" fill="none" stroke="#ea1c24" stroke-width="1.6"/><ellipse cx="8" cy="8" rx="2.8" ry="6.6" fill="none" stroke="#ea1c24" stroke-width="1.2"/><path d="M1.5 8h13" stroke="#ea1c24" stroke-width="1.2"/></svg>
          www.brightoakbuilders.com
        </li>
      </ul>
    </div>
  </section>

</main>
</body>
</html>
```